Redesign of business card for Cedar Ridge Mechanical

We are looking for a new design for our business cards for Cedar Ridge Mechanical. We are a plumbing & HVAC construction company, operating on the West Coast of Canada and USA. Logo attached.
Industry/Entity Type
Construction - Plumbing & HVAC
Contact Information for Business Card
Name, address, phone numbers, email, website address
Look and feel
Each slider illustrates characteristics of the customer's brand and the style your logo design should communicate.

```html
<!DOCTYPE html>
<html lang="en">
<head>
<meta charset="utf-8">
<title>Cedar Ridge Mechanical — Business Card</title>
<link href="https://fonts.googleapis.com/css2?family=Montserrat:wght@400;500;700&display=swap" rel="stylesheet">
<style>
  :root {
    --page-bg: #141414;
    --card-bg: #1a1a1a;
    --ink: #ffffff;
    --ink-soft: #e6e6e6;
    --rule: #bdbdbd;
  }
  * { box-sizing: border-box; margin: 0; padding: 0; }
  html, body {
    width: 1200px;
    height: 963px;
    overflow: hidden;
    background: var(--page-bg);
  }
  .stage {
    width: 1200px;
    height: 963px;
    display: flex;
    align-items: center;
    justify-content: center;
  }
  .business-card {
    position: relative;
    width: 780px;
    height: 446px;
    background: var(--card-bg);
    border-radius: 26px;
    overflow: hidden;
    font-family: "Montserrat", sans-serif;
    color: var(--ink);
    box-shadow: 0 18px 50px rgba(0,0,0,0.55);
  }
  .edge-bar {
    position: absolute;
    width: 14px;
    background: var(--ink);
  }
  .edge-bar--left { left: 58px; top: 40px; height: 250px; }
  .edge-bar--right { right: 58px; bottom: 40px; height: 200px; }

  .brand {
    position: absolute;
    left: 110px;
    top: 150px;
    width: 280px;
    display: flex;
    align-items: center;
    gap: 14px;
  }
  .brand__mark {
    flex: 0 0 auto;
    width: 46px;
    height: 46px;
    border: 4px solid var(--ink);
    border-radius: 8px;
  }
  .brand__name {
    font-weight: 700;
    font-size: 26px;
    line-height: 1.15;
    letter-spacing: 0.5px;
    text-transform: uppercase;
    color: var(--ink);
  }

  .divider {
    position: absolute;
    left: 420px;
    top: 95px;
    width: 1.5px;
    height: 260px;
    background: var(--rule);
  }

  .contact {
    position: absolute;
    left: 452px;
    top: 112px;
    width: 280px;
  }
  .contact__name {
    font-weight: 700;
    font-size: 22px;
    letter-spacing: 0.8px;
    text-transform: uppercase;
  }
  .contact__role {
    font-size: 15px;
    font-weight: 400;
    color: var(--ink-soft);
    margin-top: 2px;
  }
  .contact__address {
    font-size: 16px;
    line-height: 1.3;
    margin-top: 12px;
  }
  .contact__list {
    list-style: none;
    margin-top: 12px;
  }
  .contact__item {
    display: flex;
    align-items: center;
    gap: 8px;
    font-size: 16px;
    line-height: 1.55;
  }
  .contact__icon {
    width: 14px;
    height: 14px;
    flex: 0 0 auto;
    fill: var(--ink);
  }
</style>
</head>
<body>
<main class="stage">
  <section class="business-card" aria-label="Cedar Ridge Mechanical business card">
    <span class="edge-bar edge-bar--left"></span>
    <span class="edge-bar edge-bar--right"></span>

    <div class="brand">
      <span class="brand__mark"></span>
      <span class="brand__name">Cedar Ridge Mechanical</span>
    </div>

    <span class="divider"></span>

    <div class="contact">
      <h1 class="contact__name">Daniel Whitford</h1>
      <p class="contact__role">Manager</p>
      <p class="contact__address">Your address, city<br>state, ZIP 0000</p>
      <ul class="contact__list">
        <li class="contact__item">
          <svg class="contact__icon" viewBox="0 0 24 24" aria-hidden="true"><path d="M6.6 10.8a15.1 15.1 0 0 0 6.6 6.6l2.2-2.2a1 1 0 0 1 1-.25 11.4 11.4 0 0 0 3.6.57 1 1 0 0 1 1 1V20a1 1 0 0 1-1 1A17 17 0 0 1 3 4a1 1 0 0 1 1-1h3.5a1 1 0 0 1 1 1c0 1.25.2 2.45.57 3.6a1 1 0 0 1-.25 1z"/></svg>
          123-456-2100
        </li>
        <li class="contact__item">
          <svg class="contact__icon" viewBox="0 0 24 24" aria-hidden="true"><path d="M2 5h20v14H2z M4 7v.4l8 5 8-5V7l-8 5z" fill-rule="evenodd"/></svg>
          youremail@mailbox.com
        </li>
        <li class="contact__item">
          <svg class="contact__icon" viewBox="0 0 24 24" aria-hidden="true"><circle cx="12" cy="12" r="10"/><path d="M2 12h20M12 2c3 3 3 17 0 20M12 2c-3 3-3 17 0 20" stroke="#1a1a1a" stroke-width="1.6" fill="none"/></svg>
          www.yourwebsite.com
        </li>
      </ul>
    </div>
  </section>
</main>
</body>
</html>
```